Harwick + Pell Architect Marketing campaign for a morern fresh architecture cutting egde firm th...

To create en exciting template for our monthly newsletters to go out to all our clients via email. I have added a bit of an idea of what we like but not limited to..... we like a nice clean fresh look with lots of white space. I hve aslo added a sketch of the type of how we might layt it out - you may have a better idea. also the pics of the projects for the first issue (issue #1)We like the opening page like the attached brewlane had and replace the cup with apic of our building/office. Cant wait to see what you come up with.

Target Market(s)

young professionals

Industry/Entity Type

Architectural

Font styles to use
Serif

Colors

Designer to choose colors to be used in the design.

Requirements
Must have
• Logo, text information provided, photos provided
Nice to have
• lots of white space, clean and frest looking

```html
<!DOCTYPE html>
<html lang="en">
<head>
<meta charset="utf-8">
<title>Harwick + Pell Architecture — Newsletter Issue #1</title>
<link href="https://fonts.googleapis.com/css2?family=Raleway:wght@300;400;600;700&display=swap" rel="stylesheet">
<style>
  :root {
    --ink: #111111;
    --text: #2b2b2b;
    --paper: #ffffff;
    --dusk-top: #3a3f58;
    --dusk-mid: #5b5f74;
    --dusk-low: #2a2a2e;
    --concrete: #8d9196;
    --cedar: #a4623c;
    --badge-blue: #1f4e8c;
    --badge-grey: #8a8a8a;
  }
  * { margin: 0; padding: 0; box-sizing: border-box; }
  html, body { width: 1200px; height: 5304px; overflow: hidden; background: var(--paper); }
  body { position: relative; font-family: "Raleway", sans-serif; color: var(--text); }
  .abs { position: absolute; }

  .brand { left: 0; width: 1200px; top: 176px; display: flex; justify-content: center; align-items: center; gap: 18px; }
  .brand-dot { width: 26px; height: 26px; background: var(--ink); }
  .brand-name { font-weight: 600; font-size: 40px; letter-spacing: 3px; color: var(--ink); }

  .hero { left: 0; top: 492px; width: 1200px; height: 566px;
    background: linear-gradient(180deg, var(--dusk-top) 0%, var(--dusk-mid) 45%, var(--dusk-low) 100%); }
  .hero-title { left: 103px; top: 620px; font-weight: 700; font-size: 44px; color: #fff; letter-spacing: 0.5px; }
  .hero-text { left: 103px; top: 700px; width: 660px; font-weight: 400; font-size: 30px; line-height: 44px; color: #fff; text-align: justify; hyphens: auto; }

  .welcome-title { left: 0; width: 1200px; top: 1150px; text-align: center; font-weight: 700; font-size: 52px; color: var(--ink); }
  .welcome-text { left: 111px; width: 980px; top: 1262px; text-align: center; font-size: 28.5px; line-height: 55.5px; font-weight: 400; hyphens: auto; }

  .section-title { font-weight: 700; font-size: 54px; line-height: 56px; color: var(--ink); }
  .body-copy { font-size: 27px; line-height: 55.5px; font-weight: 400; text-align: justify; hyphens: auto; }

  .photo { display: block; }
</style>
</head>
<body>

  <header class="abs brand">
    <span class="brand-dot"></span>
    <span class="brand-name">HARWICK + PELL ARCHITECTURE</span>
  </header>

  <div class="abs hero" role="img" aria-label="Dusk photograph of the studio's new office building with lit glass frontage"></div>
  <h1 class="abs hero-title">WE’RE GLAD YOU’RE HERE</h1>
  <p class="abs hero-text">Now that you are a Harwick + Pell Architecture insider you’ll be among the first to hear about up-coming projects that the studio is working on, completed projects, news and more.</p>

  <h2 class="abs welcome-title">WELCOME</h2>
  <p class="abs welcome-text">It appears that there are a lot of people are genuinely interested in the building and construction industry, and we here at Harwick + Pell Architecture often get asked “what we are up to” and “what cool projects have we got on the go”. With that being said we thought we would share with you some of our projects at various stages for you all to enjoy.</p>

  <h2 class="abs section-title" style="left:101px; top:1712px;">ON THE DRAWING<br>BOARD</h2>
  <p class="abs body-copy" style="left:101px; top:1870px; width:500px;">We have recently completed this two story house concept overlooking the canals at Lake Arden here in Marlow. We are currently in the Working Drawing phase at present. This house will stand out from the crowd and has a mixture of cedar, standing seam wall cladding and precast concrete panels. We are really excited to see this project to progress to construction. We will keep you posted on this one!!</p>
  <div class="abs photo" style="left:689px; top:1760px; width:404px; height:335px; background:linear-gradient(180deg,#6f7394 0%,#9a98a8 55%,#2f2f33 100%);" role="img" aria-label="Concept render of a dark clad building at dusk"></div>
  <div class="abs photo" style="left:689px; top:2130px; width:404px; height:334px; background:linear-gradient(180deg,#b9bcc0 0%,#9a9da1 55%,#5e6064 100%);" role="img" aria-label="Building facade with site cones and a scissor lift"></div>

  <h2 class="abs section-title" style="left:597px; width:502px; top:2632px; text-align:right;">UNDER<br>CONSTRUCTION</h2>
  <div class="abs photo" style="left:103px; top:2677px; width:403px; height:336px; background:linear-gradient(90deg,#4a4a4c 0%,var(--cedar) 45%,#9a9a9c 100%);" role="img" aria-label="Two storey building with curved cedar cladding under construction"></div>
  <div class="abs photo" style="left:103px; top:3048px; width:403px; height:333px; background:linear-gradient(180deg,#c9cbcd 0%,var(--concrete) 55%,#6d6f72 100%);" role="img" aria-label="Concrete and cedar facade with construction cones"></div>
  <p class="abs body-copy" style="left:597px; top:2793px; width:500px;">We have recently completed this two story house concept overlooking the canals at Lake Arden here in Marlow. We are currently in the Working Drawing phase at present. This house will stand out from the crowd and has a mixture of cedar, standing seam wall cladding and precast concrete panels. We are really excited to see this project to progress to construction. We will keep you posted on this one!!</p>

  <h2 class="abs section-title" style="left:101px; top:3598px;">FEATURE PROJECT</h2>
  <div class="abs photo" style="left:101px; top:3750px; width:403px; height:337px; background:linear-gradient(180deg,#4e5372 0%,#6d6f80 45%,#2b2b2f 100%);" role="img" aria-label="Office and factory building lit at dusk"></div>
  <div class="abs photo" style="left:101px; top:4120px; width:403px; height:336px; background:linear-gradient(180deg,#53577a 0%,#74768a 45%,#2a2a2e 100%);" role="img" aria-label="Factory entrance with glowing windows at dusk"></div>
  <p class="abs body-copy" style="left:597px; top:3702px; width:502px;">This new office and factory located in the new Marlow Business Park is comprised of a large Cutting and Processing facility for the manufacturer of steel plate profiles. The facility 1,500m² houses two 10-tonne gantry cranes running the full length of the 60 x 25 metre workshop and was designed with the emphasis on maximum plate storage and profile cutting efficiency. Alongside the processing facility is an attached 238m² modern single level office building has been designed to project the character and brand of Keystone Cutting and to sit within the</p>

  <h3 class="abs" style="left:0; width:1200px; top:4702px; text-align:center; font-weight:600; font-size:32px; color:var(--ink);">STAY CONNECTION WITH US</h3>
  <p class="abs" style="left:103px; width:998px; top:4780px; text-align:center; font-size:30px; line-height:44px;">Also remember to follow us on our social media platforms where are keeping our followers up to date frequently.</p>

  <div class="abs" style="left:542px; top:4921px; width:37px; height:37px; background:var(--ink); border-radius:6px;" aria-label="Social profile"></div>
  <div class="abs" style="left:624px; top:4921px; width:37px; height:37px; background:var(--ink); border-radius:6px;" aria-label="Social profile"></div>

  <div class="abs" style="left:257px; top:5011px; width:330px; height:128px; background:var(--badge-blue); border-radius:6px;" aria-label="Industry association badge"></div>
  <div class="abs" style="left:716px; top:5002px; width:206px; height:150px; background:var(--badge-grey); border-radius:6px;" aria-label="Professional member badge"></div>

  <p class="abs" style="left:0; width:1342px; top:5216px; text-align:center; font-size:20px; color:var(--ink);">COPYRIGHTS. ALL RIGHTS RESERVED</p>

</body>
</html>
```